A clean crisp business card for a Landscape Construction company. Designed to be easy to read contact/ info and also be appealing/interesting, unlike a traditional business card.

Industry/Entity Type

Landscape Construction

Contact Information for Business Card

Company name : Brambleford Landscape Construction, phone number: (877) 62Vista, website:Bramblefordyards.example, Email, sales@bramblefordyards.example

Requirements
Nice to have
• Luxurious finishes/ details…. Icons or emblems next to contact info
Should not have
• Clipart or general pictures

```html
<!DOCTYPE html>
<html lang="en">
<head>
<meta charset="utf-8">
<title>Brambleford Landscape Construction – Business Card</title>
<link rel="stylesheet" href="https://fonts.googleapis.com/css2?family=Montserrat:wght@400;500;700;800&display=swap">
<style>
  :root {
    --bg: #d4d4d4;
    --card-blue: #1f6bb5;
    --deep-blue: #1a4f94;
    --leaf-green: #8dc63f;
    --white: #ffffff;
    --ink-light: #eef4fb;
  }
  * { box-sizing: border-box; margin: 0; padding: 0; }
  html, body { width: 1200px; height: 788px; overflow: hidden; }
  body {
    background: var(--bg);
    font-family: "Montserrat", Arial, sans-serif;
    position: relative;
  }
  .card {
    position: absolute;
    border-radius: 22px;
    overflow: hidden;
    background: var(--card-blue);
    box-shadow: 0 10px 24px rgba(0,0,0,0.25);
  }
  /* Contact side (portrait) */
  .card--contact { left: 110px; top: 104px; width: 340px; height: 580px; }
  .contact-block {
    position: absolute; top: 42px; right: 30px; left: 30px;
    text-align: right; color: var(--ink-light);
  }
  .person-name {
    color: var(--leaf-green); font-weight: 800; font-size: 25px;
    letter-spacing: 0.5px; text-transform: uppercase;
  }
  .person-title { font-size: 15px; margin-top: 2px; }
  .rule { width: 14px; height: 2px; background: var(--leaf-green); margin: 10px 0 12px auto; }
  .address { font-size: 13.5px; line-height: 1.45; margin-bottom: 10px; }
  .contact-line {
    display: flex; justify-content: flex-end; align-items: center; gap: 7px;
    font-size: 13.5px; line-height: 1.55;
  }
  .contact-line svg { width: 12px; height: 12px; flex: none; }
  .contact-foot {
    position: absolute; left: 0; bottom: 0; width: 340px; height: 260px;
  }
  .wordmark-stack {
    position: absolute; left: 24px; bottom: 34px;
    color: var(--deep-blue); font-weight: 700; font-size: 15px;
    line-height: 1.3; letter-spacing: 0.3px;
  }
  .wordmark-stack .wm-lead { font-size: 26px; line-height: 1.15; }
  /* Brand side (landscape) */
  .card--brand { left: 500px; top: 229px; width: 590px; height: 340px; }
  .brand-wordmark {
    position: absolute; inset: 0; display: flex; align-items: center; justify-content: center;
    gap: 14px; color: var(--white); font-weight: 700;
  }
  .brand-wordmark .mark-dot { width: 22px; height: 22px; border-radius: 50%; background: var(--white); flex: none; }
  .brand-wordmark .wm-text { font-size: 24px; letter-spacing: 1px; line-height: 1.3; }
  .brand-wordmark .wm-text span { display: block; font-size: 38px; }
</style>
</head>
<body>

<section class="card card--contact" aria-label="Business card, contact side">
  <div class="contact-block">
    <p class="person-name">Dana Whitlow</p>
    <p class="person-title">Founder</p>
    <div class="rule"></div>
    <p class="address">412 N. Hollis Lane<br>Country Name, AB 35412</p>
    <p class="contact-line">(877) 62Vista
      <svg viewBox="0 0 12 12" aria-hidden="true"><path d="M2 4c0-1.2 1.8-2 4-2s4 .8 4 2l-1.5 1L7 4H5L3.5 5Z M3 6h6l1 4H2Z" fill="var(--leaf-green)"/></svg>
    </p>
    <p class="contact-line">sales@bramblefordyards.example
      <svg viewBox="0 0 12 12" aria-hidden="true"><rect x="1" y="2.5" width="10" height="7" rx="1" fill="var(--leaf-green)"/><path d="M1.5 3 6 6.5 10.5 3" stroke="var(--card-blue)" fill="none"/></svg>
    </p>
    <p class="contact-line">bramblefordyards.example
      <svg viewBox="0 0 12 12" aria-hidden="true"><circle cx="6" cy="6" r="5" fill="var(--leaf-green)"/><path d="M1 6h10M6 1c-2 2.5-2 7.5 0 10M6 1c2 2.5 2 7.5 0 10" stroke="var(--card-blue)" stroke-width="0.8" fill="none"/></svg>
    </p>
  </div>

  <svg class="contact-foot" viewBox="0 0 340 260" aria-hidden="true">
    <path d="M0 30 C 150 30, 260 120, 300 200 C 315 228, 328 245, 340 252 L 340 260 L 0 260 Z" fill="var(--white)"/>
    <path d="M0 30 C 150 30, 260 120, 300 200 C 315 228, 328 245, 340 252" stroke="var(--leaf-green)" stroke-width="5" fill="none"/>
  </svg>
  <p class="wordmark-stack"><span class="wm-lead">Brambleford</span><br>Landscape Construction</p>
</section>

<section class="card card--brand" aria-label="Business card, brand side">
  <div class="brand-wordmark">
    <span class="mark-dot"></span>
    <p class="wm-text"><span>Brambleford</span>Landscape Construction</p>
  </div>
</section>

</body>
</html>
```